Hello my Name is Elias Moreno. I buy and sell vintage comic books, you can refer to my instragram page qpkz.comics to get ideas and inspiration. For the front of the card I would like my company logo QPKZ Comics with a yellow and black background with the bat signal or bat emblem like on my IG page and with my info Elias Moreno as the Owner and address/ phone number, PO Box 617283, Miami, FL 33827, 305-482-6170 and that I buy and sell comics & collectables . Also feel free to be open to other ideas if you want. Im not stuck on one design. For the back of the card I would like for it to say follow me on Instagram QPKZ.Comics with the ig emblem. Also would like the card to be vertical if possible. Thanks

```html
<!DOCTYPE html>
<html lang="en">
<head>
<meta charset="utf-8">
<title>QPKZ Comics – Business Card</title>
<link rel="stylesheet" href="https://fonts.googleapis.com/css2?family=Lato:ital,wght@0,400;0,700;0,900;1,700&display=swap">
<style>
  :root {
    --backdrop: #3b3431;
    --card-black: #050505;
    --card-sheen: #1e1e1e;
    --brand-yellow: #fcc313;
    --ink-white: #f2f2f2;
    --tab-silver: #d9d9d9;
  }
  * { box-sizing: border-box; margin: 0; padding: 0; }
  html, body {
    width: 1200px; height: 844px; overflow: hidden;
    background: var(--backdrop);
    font-family: "Lato", "Helvetica Neue", Arial, sans-serif;
  }
  .stage {
    position: relative; width: 1200px; height: 844px;
    display: flex; align-items: center; justify-content: center; gap: 60px;
  }
  .card {
    position: relative; width: 520px; height: 297px; overflow: hidden;
    background: var(--card-black);
    box-shadow: 0 14px 30px rgba(0,0,0,.45);
  }

  /* Contact side */
  .card--contact {
    background: linear-gradient(100deg, var(--card-black) 0%, var(--card-black) 55%, var(--card-sheen) 100%);
  }
  .band { position: absolute; left: 0; right: 0; background: var(--brand-yellow); }
  .band--top { top: 0; height: 11px; }
  .band--bottom { bottom: 24px; height: 11px; }
  .contact {
    position: absolute; left: 0; right: 0; top: 48px;
    text-align: center; color: var(--ink-white);
  }
  .contact__name { font-weight: 900; font-size: 19px; color: var(--brand-yellow); }
  .contact__role { font-size: 13px; margin-top: 2px; }
  .contact__phone { font-size: 14px; margin-top: 22px; }
  .contact__address { font-size: 14px; margin-top: 22px; }
  .contact__tagline {
    font-weight: 700; font-style: italic; font-size: 21px;
    color: var(--brand-yellow); margin-top: 30px;
  }

  /* Brand side */
  .card--brand {
    background: radial-gradient(circle at 45% 45%, #1c1c1c 0%, var(--card-black) 65%);
  }
  .tab {
    position: absolute; width: 28px; height: 34px;
    background: var(--brand-yellow);
  }
  .tab::before {
    content: ""; position: absolute; top: 0; bottom: 0; width: 4px;
    background: var(--tab-silver);
  }
  .tab--right { right: 0; top: 22px; }
  .tab--right::before { left: 0; }
  .tab--left { left: 0; top: 205px; }
  .tab--left::before { right: 0; }
  .brand-name {
    position: absolute; left: 150px; top: 112px;
    display: flex; align-items: center; gap: 10px;
  }
  .brand-name__dot {
    width: 34px; height: 34px; border-radius: 50%;
    background: var(--brand-yellow);
  }
  .brand-name__text {
    font-weight: 900; font-size: 30px; color: var(--brand-yellow); letter-spacing: .5px;
  }
  .social {
    position: absolute; right: 44px; top: 170px;
  }
  .social__lead { font-weight: 700; font-size: 13px; color: var(--brand-yellow); }
  .social__handle {
    display: flex; align-items: center; gap: 6px; margin-top: 8px;
    font-size: 13px; color: var(--ink-white);
  }
  .social__dot {
    width: 16px; height: 16px; border-radius: 50%; background: var(--brand-yellow);
  }
</style>
</head>
<body>
  <main class="stage">
    <section class="card card--contact" aria-label="Contact side">
      <div class="band band--top"></div>
      <div class="contact">
        <p class="contact__name">Elias Moreno</p>
        <p class="contact__role">Owner</p>
        <p class="contact__phone">305-482-6170</p>
        <p class="contact__address">PO Box 617283&nbsp; Miami, FL 33827</p>
        <p class="contact__tagline">We buy and sell comics &amp; collectables</p>
      </div>
      <div class="band band--bottom"></div>
    </section>

    <section class="card card--brand" aria-label="Brand side">
      <div class="tab tab--right"></div>
      <div class="tab tab--left"></div>
      <div class="brand-name">
        <span class="brand-name__dot"></span>
        <span class="brand-name__text">QPKZ Comics</span>
      </div>
      <div class="social">
        <p class="social__lead">Follow me on</p>
        <p class="social__handle"><span class="social__dot"></span>QPKZ.Comics</p>
      </div>
    </section>
  </main>
</body>
</html>
```